Bright Harbor, LLC Business Card Design

We need a product business card designed for a new company Bright Harbor, LLC. We make and resell waterless RV cleaner, polish and protectant. It cleans and protects in a simple spray and wipe step leaving the surface protected and conditioned to repel dust, dirt, water, smudges, bugs and fingerprints while preventing fogging. Safe on acrylic, plexiglas, lexan, plastic, rubber, painted surfaces, chrome, stainless, aluminum, vinyl, leather, glass.... This is an eco-friendly green product.

We want to play off the company name to tell the consumer that the product is easy to use and associate to the nostalgics 1950's in the USA... Thinking old travel trailer with hot rod truck pulling it as the graphic, maybe the husband cleaning the truck and the wife cleaning the trailer for a Bright Harbor surface.
Updates

Just posted our newly finished logo. Need to have "Cleaner and Protectant" added to the design as well. Thanks everyone that has submitted thus far, i am working to get comments on all.

If you need a different file format, please let me know. Thank you.

Most important info, is the logo, website and the words "Cleaner" or "Clean" along "Protectant" or "Protect" the remainder is of less importance. Highlight: www.brightharborwash.example Focus is on company brand for Brighter Harbor Cleaner product: However, need a section for the following contact info: Walt Ferris (xxx) xxx-xxxx email address Would like space for QR Code if possible.

Target Market(s)

Adults in the USA between ages of 35-75 that are actively involved in the Recreational Vehicle (RV), travel trailer, and hot rod lifestyle. We are targeting the RV marked of the high end travel, 5th wheel and bus RV market. Along with hot rods, automotive and motorcycle market.

Industry/Entity Type

Travel

Requirements
Must have
• Most important info, is the logo, website and the words "Cleaner" or "Clean" along "Protectant" or "Protect" the remainder is of less importance.

Highlight:
www.brightharborwash.example

Focus is on company brand for Brighter Harbor Cleaner product: However, need a section for the following contact info:

Walt Ferris
(xxx) xxx-xxxx
email address
Nice to have
• Would like a space for a QR Code.

```html
<!DOCTYPE html>
<html lang="en">
<head>
<meta charset="utf-8">
<title>Bright Harbor, LLC – Business Card</title>
<link rel="stylesheet" href="https://fonts.googleapis.com/css2?family=Oswald:wght@600&family=Exo+2:wght@400;500&display=swap">
<style>
  :root {
    --stage: #e4e4e4;
    --card-white: #fbfbfb;
    --card-shade: #ececec;
    --swoosh-grey: #8a8a8a;
    --swoosh-dark: #5e5e5e;
    --blue-deep: #2458b8;
    --blue-bright: #1898e0;
    --ink-dark: #1e1e1e;
    --ink-soft: #4a4a4a;
    --ink-light: #ffffff;
  }
  * { box-sizing: border-box; margin: 0; padding: 0; }
  html, body {
    width: 1200px; height: 900px; overflow: hidden;
    background: var(--stage);
  }
  .business-card {
    position: absolute;
    left: 180px; top: 210px;
    width: 840px; height: 480px;
    background: linear-gradient(160deg, var(--card-white) 40%, var(--card-shade));
    box-shadow: 0 18px 40px rgba(0,0,0,.18);
    overflow: hidden;
  }
  .card-artwork { position: absolute; inset: 0; }
  .brand-block {
    position: absolute;
    left: 48px; top: 252px;
  }
  .brand-name {
    font-family: "Oswald", sans-serif;
    font-weight: 600;
    font-size: 46px;
    line-height: 1.1;
    letter-spacing: 1px;
    text-transform: uppercase;
    color: var(--ink-dark);
  }
  .brand-tagline {
    margin-top: 4px;
    font-family: "Exo 2", sans-serif;
    font-weight: 500;
    font-size: 17px;
    letter-spacing: 3px;
    text-transform: uppercase;
    color: var(--ink-soft);
  }
  .contact-panel {
    position: absolute;
    right: 32px; top: 34px;
    width: 300px;
    text-align: right;
    color: var(--ink-light);
    font-family: "Exo 2", sans-serif;
  }
  .person-name {
    font-size: 30px; font-weight: 500;
    letter-spacing: 2px; text-transform: uppercase;
    line-height: 1.1;
  }
  .person-title { font-size: 16px; letter-spacing: 1px; margin-bottom: 34px; }
  .address { font-size: 17px; line-height: 1.35; margin-bottom: 28px; letter-spacing: .5px; }
  .contact-line {
    display: flex; justify-content: flex-end; align-items: center;
    gap: 10px; font-size: 15px; line-height: 1.65; letter-spacing: .3px;
    white-space: nowrap;
  }
  .contact-line svg { flex: none; width: 15px; height: 15px; fill: none; stroke: var(--ink-light); stroke-width: 1.6; }
  .contact-line svg .solid { fill: var(--ink-light); stroke: none; }
</style>
</head>
<body>
  <div class="business-card">
    <svg class="card-artwork" viewBox="0 0 840 480" width="840" height="480" aria-hidden="true">
      <defs>
        <linearGradient id="blueField" x1="0" y1="1" x2="1" y2="0">
          <stop offset="0" stop-color="var(--blue-deep)"/>
          <stop offset="1" stop-color="var(--blue-bright)"/>
        </linearGradient>
        <linearGradient id="greySwoosh" x1="0" y1="0" x2="0" y2="1">
          <stop offset="0" stop-color="var(--swoosh-grey)"/>
          <stop offset="1" stop-color="var(--swoosh-dark)"/>
        </linearGradient>
      </defs>
      <path class="swoosh" d="M305,0 C440,110 470,300 420,480 H443 C485,300 470,120 350,0 Z" fill="url(#greySwoosh)"/>
      <path class="blue-field" d="M360,0 H840 V480 H453 C497,300 482,118 360,0 Z" fill="url(#blueField)"/>
    </svg>

    <div class="brand-block">
      <div class="brand-name">Bright Harbor</div>
      <div class="brand-tagline">Cleaner &amp; Protectant</div>
    </div>

    <div class="contact-panel">
      <div class="person-name">Walt Ferris</div>
      <div class="person-title">Managing Director</div>
      <div class="address">041, 12th floor, Pier<br>Landing Road BHR</div>
      <div class="contact-line">555 014 2230
        <svg viewBox="0 0 16 16"><path d="M4 2 L6 5 L4.8 6.5 C5.8 8.6 7.4 10.2 9.5 11.2 L11 10 L14 12 L12.5 14 C7 13.5 2.5 9 2 3.5 Z"/></svg>
      </div>
      <div class="contact-line">555 014 2231
        <svg viewBox="0 0 16 16"><rect x="4" y="1.5" width="8" height="13" rx="1.5"/><circle class="solid" cx="8" cy="12" r="0.9"/></svg>
      </div>
      <div class="contact-line">555 014 2232
        <svg viewBox="0 0 16 16"><rect class="solid" x="2" y="6" width="12" height="8" rx="1"/><rect x="5" y="2" width="6" height="4"/></svg>
      </div>
      <div class="contact-line">walt@brightharborwash.example
        <svg viewBox="0 0 16 16"><rect class="solid" x="1.5" y="3.5" width="13" height="9" rx="1"/><path d="M1.5 4 L8 9 L14.5 4" stroke="#2a6cc8"/></svg>
      </div>
      <div class="contact-line">www.brightharborwash.example
        <svg viewBox="0 0 16 16"><circle cx="8" cy="8" r="6"/><ellipse cx="8" cy="8" rx="2.6" ry="6"/><path d="M2 8 H14 M3 5 H13 M3 11 H13"/></svg>
      </div>
    </div>
  </div>
</body>
</html>
```